Property management company looking for modern card design

We at Blue Heron Partners provides property management services for its residential and commercial properties, with expertise in all categories of multifamily, industrial and office projects throughout California.

We need a business card design that is professional and modern designed business card. In our field, clients get hundreds of business cards, we would like our card to stand out.

Please avoid small print.

Target Market(s)

Professionals and high end clients

Industry/Entity Type

Financial Planning

Contact Information for Business Card

Company Name: Blue Heron Partners, Name, email, license #, phone number, website blueheronpartners.com

Font styles to use
Sans Serif

Requirements
Must have
• The card design needs to be adaptable because there is a possibly we will be expanding into different sectors other than real estate. The card design should be focused on financial planning and asset management.
Nice to have
• Modern and simple business card. Eye catching. Non-standard size/shaped cards would be great.
• blueheronpartners.com
Should not have
• Too many bright color or any pictures or shapes of real estate stuff.

```html
<!DOCTYPE html>
<html lang="en">
<head>
<meta charset="utf-8">
<title>Blue Heron Partners – Business Card</title>
<link rel="stylesheet" href="https://fonts.googleapis.com/css2?family=Open+Sans:wght@300;400;600;700&display=swap">
<style>
  :root {
    --backdrop: #3b3430;
    --card: #0d0d0d;
    --card-edge: #1c1c1c;
    --accent: #e3162b;
    --accent-deep: #a50d1c;
    --text-light: #f2f2f2;
    --text-silver: #d9d9d9;
  }
  * { margin: 0; padding: 0; box-sizing: border-box; }
  html, body {
    width: 1200px; height: 900px; overflow: hidden;
    background: var(--backdrop);
    font-family: "Open Sans", Arial, sans-serif;
  }
  .canvas {
    position: relative; width: 1200px; height: 900px;
    display: flex; align-items: center; justify-content: center; gap: 60px;
  }
  .card {
    position: relative; width: 520px; height: 297px;
    background: var(--card);
    border: 1px solid var(--card-edge);
    box-shadow: 0 18px 40px rgba(0,0,0,0.55);
  }
  /* Contact side */
  .card-back .mark-circle {
    position: absolute; left: 48px; top: 58px;
    width: 180px; height: 180px; border-radius: 50%;
    background: var(--accent);
  }
  .card-back .divider {
    position: absolute; left: 262px; top: 40px;
    width: 1px; height: 217px;
    background: linear-gradient(to bottom, transparent, var(--accent-deep) 40%, var(--accent-deep) 60%, transparent);
  }
  .contact {
    position: absolute; left: 284px; top: 62px; color: var(--text-light);
  }
  .contact .name { color: var(--accent); font-weight: 700; font-size: 17px; line-height: 1.2; }
  .contact .role { font-size: 13px; margin-top: 2px; }
  .contact .license { font-size: 14px; margin-top: 28px; }
  .contact .license-label { color: var(--accent); font-weight: 700; }
  .contact-list { list-style: none; margin-top: 18px; }
  .contact-list li {
    display: flex; align-items: center; gap: 9px;
    font-size: 13.5px; line-height: 22px;
  }
  .contact-list svg { width: 11px; height: 11px; fill: var(--accent); flex: none; }
  /* Logo side */
  .card-front { display: flex; flex-direction: column; align-items: center; justify-content: center; }
  .card-front .logo-circle {
    width: 84px; height: 84px; border-radius: 50%;
    background: var(--accent); margin-bottom: 22px;
  }
  .card-front .company-name {
    color: var(--text-silver); font-weight: 400;
    font-size: 38px; line-height: 1.1; text-align: center; letter-spacing: -0.5px;
  }
</style>
</head>
<body>
<main class="canvas">
  <section class="card card-back" aria-label="Contact side">
    <div class="mark-circle"></div>
    <div class="divider"></div>
    <div class="contact">
      <p class="name">Daniel Mercer</p>
      <p class="role">Managing Director</p>
      <p class="license"><span class="license-label">License:</span> BHP07318</p>
      <ul class="contact-list">
        <li>
          <svg viewBox="0 0 24 24" aria-hidden="true"><path d="M6.6 10.8a15.1 15.1 0 0 0 6.6 6.6l2.2-2.2a1 1 0 0 1 1-.25 11.4 11.4 0 0 0 3.6.57 1 1 0 0 1 1 1V20a1 1 0 0 1-1 1A17 17 0 0 1 3 4a1 1 0 0 1 1-1h3.5a1 1 0 0 1 1 1c0 1.25.2 2.45.57 3.57a1 1 0 0 1-.25 1z"/></svg>
          044-987 654 321
        </li>
        <li>
          <svg viewBox="0 0 24 24" aria-hidden="true"><path d="M2 5h20v14H2z M2 5l10 8 10-8" fill="none" stroke="#e3162b" stroke-width="0"/><path d="M2 6.5 12 13l10-6.5V19H2z"/><path d="M2 5h20l-10 6.5z"/></svg>
          info@blueheronpartners.com
        </li>
        <li>
          <svg viewBox="0 0 24 24" aria-hidden="true"><circle cx="12" cy="12" r="10"/></svg>
          www.blueheronpartners.com
        </li>
      </ul>
    </div>
  </section>

  <section class="card card-front" aria-label="Logo side">
    <div class="logo-circle"></div>
    <p class="company-name">Blue Heron<br>Partners</p>
  </section>
</main>
</body>
</html>
```